Web Design / Transformation our Joomla web site

Job Type
We are looking for a fresh eye-catching Custom Joomla Design to transform our Joomla web site

Task Description
We are in a process to create web site to Speech Pathology services . The site is built by using brightpanel ((http://www.brightpanel-demo.com/) meadow template.

You can see our site http://beyondtalkclinic-demo.com/demo

Unfortunately, this template does not match our identity. We would like to improve or replace it. Although we like features that brightpanel template is giving as part of their template ,we want to transform our site to something more simplistic and kids oriented . We don’t like look and fill of our website since it’s very professional and “corporate” . Our business is very small and is not 100 people company , we are looking for something more simple and personal. It should look professional, all be it, child friendly. We work on children’s communication skills, and we want to convey an idea that communication is “Beyond The Talk”, meaning children need to learn to play and socialize appropriately. In addition, learning to be a better communicators will help them to be closer to their family members and friends. We want our website to show kids playing and having fun. In other hand , we don't want the Website to be too busy with images, so use your professional judgment.
You can change current template or you can provide your own Joomla design.

Examples of website look that we like :

http://parentvoicehelp-demo.com
http://thevocalfriends-demo.blogspot.com/
http://brindleclinicvoice-demo.com/

About Our Company :
Company name: Beyond The Talk
What we do: Pediatric Speech & Language Pathology Services. We established Beyond The Talk to provide families with a unique option for their child’s speech therapy needs. Our clinic is founded on the principle that all children are different and require a thoughtful, parent-driven therapy plan. When a family chooses us, they will enter a partnership with an experienced, well-trained therapist.
Top Three Things to Communicate through our Website:
#1 - We are kids friendly
#2 - We are professional
#3 - We provide our services with a loving, nurturing attitude toward the child and with compassionate, comprehensive support and input for the family
Updates

To see current running site : http://beyondtalkclinic-demo.com/demo/

Reason: There are no good designs to address our needs

Reason: It's still work in progress. Submitted designs are still under constructions and waiting for updates

We are accepting WordPress designs as well !!!

Target Market(s)

Families with kids

Industry/Entity Type

Communication

Requirements
Must have
• • Joomla/Wordpress as a platform
• Easy to Navigate
• Clean Design, kids friendly but professional

```html
<!DOCTYPE html>
<html lang="en">
<head>
<meta charset="utf-8">
<title>Beyond The Talk – Speech &amp; Language Pathology Services</title>
<link rel="stylesheet" href="https://fonts.googleapis.com/css2?family=Crimson+Pro:wght@600;700&family=Arimo:wght@400;700&display=swap">
<style>
:root{
  --sky-top:#bfe3ea;--sky-bottom:#e3f3f6;
  --green:#6aab2e;--green-dark:#4e8a1c;--green-text:#5e9d25;
  --blue:#2799d0;--blue-dark:#1a6f9c;--blue-text:#2a7fb8;
  --red:#d7322c;--nav:#2c7fa8;--text:#555;--muted:#8a8a8a;
  --line:#e3e3e3;--bar:#f1f1f1;
}
*{margin:0;padding:0;box-sizing:border-box}
html,body{width:960px;height:1200px;overflow:hidden}
body{position:relative;background:linear-gradient(var(--sky-top),var(--sky-bottom) 60%,#eef8f9);font-family:"Arimo",Arial,sans-serif;color:var(--text);font-size:8.2px}
.serif{font-family:"Crimson Pro",Georgia,serif}
.abs{position:absolute}
.page{position:absolute;left:186px;top:90px;width:588px;height:986px;background:#fff;border-top:3px solid var(--green)}
.logo{left:194px;top:18px;width:150px}
.logo .name{font-family:"Crimson Pro",Georgia,serif;font-weight:700;font-size:30px;line-height:30px;color:var(--red)}
.tagline{left:197px;top:104px;font-size:7px;font-weight:700;color:var(--blue-dark);white-space:nowrap}
.logo-dot{display:inline-block;width:14px;height:14px;border-radius:50%;background:var(--red);vertical-align:middle;margin-right:6px}
.search{left:608px;top:52px;width:156px;height:22px;background:#fff;border:1px solid #d8e6ea;padding:5px 8px;color:#aaa;font-size:7.5px}
.search i{position:absolute;right:4px;top:4px;width:14px;height:13px;background:var(--blue);border-radius:2px}
.nav{left:360px;top:93px;display:flex;gap:0}
.nav a{font-family:"Crimson Pro",Georgia,serif;font-weight:700;font-size:9px;color:var(--nav);text-decoration:none;padding:7px 0 0;margin-right:26px;letter-spacing:.3px}
.nav a.active{color:var(--red);border-top:3px solid var(--red);padding-top:4px}
.slider{left:192px;top:122px;width:576px;height:214px;background:#ececec;border:1px solid #ddd;padding:4px}
.slide{position:relative;width:100%;height:100%;background:linear-gradient(90deg,#f6f9f1 0%,#f1f6e8 55%,#dfeccf 100%)}
.slide .photo{position:absolute;right:0;top:0;width:230px;height:100%;background:linear-gradient(110deg,#eef3e4,#e9c9b1 45%,#d9e6bf 75%,#a8c46e)}
.slide h1{position:absolute;left:30px;top:34px;font-size:18px;font-weight:700;color:var(--green-text);line-height:18px}
.slide h2{position:absolute;left:30px;top:56px;font-size:12.5px;font-weight:700;color:var(--red)}
.slide p{position:absolute;left:30px;top:78px;width:230px;font-size:7.5px;line-height:13.3px;color:#555}
.btn{position:absolute;left:30px;top:127px;background:var(--green);color:#fff;font-family:"Crimson Pro",Georgia,serif;font-weight:700;font-size:8.5px;padding:6px 8px;border-radius:2px;border:1px solid var(--green-dark)}
.dots{position:absolute;left:30px;top:175px;display:flex;gap:5px}
.dots i{width:8px;height:8px;border-radius:50%;background:#777}
.dots i:first-child{background:#444}
.quote{left:186px;top:350px;width:588px;text-align:center;font-family:"Crimson Pro",Georgia,serif;font-weight:600;font-size:10.5px;line-height:19px;color:#777;letter-spacing:.2px}
.rule{left:192px;top:396px;width:576px;height:1px;background:var(--line)}
.side-bg{left:604px;top:397px;width:170px;height:679px;background:#f7f7f7}
.band{position:absolute;height:27px;color:#fff;font-family:"Crimson Pro",Georgia,serif;font-weight:700;font-size:12.5px;padding:5px 14px;letter-spacing:.3px}
.band::after{content:"";position:absolute;right:0;top:0;border-style:solid;border-width:0 12px 12px 0;border-color:transparent var(--fold) transparent transparent}
.band.blue{background:var(--blue);--fold:#fff}
.band.green{background:var(--green);--fold:#f7f7f7;padding-left:9px}
.post{position:absolute;left:198px;width:394px}
.post h3{font-size:12.5px;font-weight:700;color:var(--green-text);margin-left:12px;position:relative}
.post h3::before{content:"›";position:absolute;left:-13px;top:-2px;font-size:14px;color:var(--green-text)}
.post p{font-size:7.4px;line-height:13.2px;margin:5px 0 0 13px;text-align:justify;color:#555}
.media{display:flex;gap:16px;margin:12px 0 0 13px}
.media .img{flex:none;width:162px;height:102px;border:1px solid #ddd;background:linear-gradient(120deg,#c9d3dc,#f2e2d4 50%,#e7c9ad)}
.media p{margin:0;text-align:justify}
.share{position:absolute;left:211px;width:380px;height:28px;background:var(--bar);border:1px solid #e4e4e4;display:flex;align-items:center;padding:0 9px;gap:5px}
.share .more{font-family:"Crimson Pro",Georgia,serif;font-weight:700;font-size:9px;color:var(--red);margin-right:22px}
.sbtn{display:flex;align-items:center;font-size:6.4px;gap:2px}
.sbtn b{background:#fff;border:1px solid #ccc;padding:1px 4px;border-radius:2px;font-weight:400;color:var(--blue-dark)}
.sbtn b.red{background:#e05b3d;color:#fff;border-color:#c84a2e}
.sbtn span{background:#fff;border:1px solid #ccc;padding:1px 3px;color:#555;margin-right:6px}
.share .date{margin-left:auto;font-size:7.5px;color:#666}
.pages{left:412px;top:1052px;display:flex;gap:9px;font-size:7px;color:var(--blue-text)}
.pages span::after{content:"›";color:#ccc;margin-left:4px}
.pages .cur{color:var(--red)}
.badge{position:absolute;left:624px;width:132px;border-radius:4px}
.recent{position:absolute;left:620px;width:146px}
.recent h4{font-size:7.6px;font-weight:400;color:var(--blue-text);position:relative;padding-left:12px}
.recent h4::before{content:"";position:absolute;left:1px;top:2px;border-left:4px solid var(--blue-text);border-top:3px solid transparent;border-bottom:3px solid transparent}
.recent p{font-size:6.8px;line-height:9.6px;color:#777;padding-left:12px;margin-top:4px}
.recent small{display:block;font-size:6.4px;color:#444;padding-left:12px;margin-top:4px}
.contact{left:621px;font-size:6.8px;color:#777;white-space:nowrap}
.contact b{font-weight:400;color:var(--blue-text);display:inline-block;width:32px}
.foot-links{left:186px;top:1088px;font-size:7.5px;color:#444}
.foot-links span{margin:0 5px;color:#777}
.copy{left:186px;top:1107px;font-size:7.5px;color:#444}
.social{left:653px;top:1094px;display:flex;gap:10px}
.social i{width:17px;height:17px;border-radius:2px}
.hills{left:0;top:1110px;width:960px;height:90px}
</style>
</head>
<body>
<svg class="abs hills" role="img" aria-label="Rolling green hills with small trees" viewBox="0 0 960 90" preserveAspectRatio="none">
  <defs><linearGradient id="hill" x1="0" y1="0" x2="0" y2="1"><stop offset="0" stop-color="#a6cf45"/><stop offset="1" stop-color="#6fa624"/></linearGradient></defs>
  <path d="M0 22 C120 0 240 6 330 30 C420 10 520 8 620 28 C720 4 860 2 960 20 V90 H0Z" fill="#b8d95e"/>
  <path d="M0 48 C160 20 300 30 420 60 C540 30 700 24 960 44 V90 H0Z" fill="url(#hill)"/>
</svg>

<div class="page"></div>

<div class="abs logo">
  <div class="name"><span class="logo-dot"></span>Beyond The Talk</div>
</div>
<div class="abs tagline">Speech &amp; Language Pathology Services</div>

<div class="abs search">Search<i></i></div>

<nav class="abs nav">
  <a class="active">HOME</a><a>ABOUT</a><a>TREATMENT TECHNIQUES</a><a>BLOG</a><a>FAQ</a><a>RESOURCES</a>
</nav>

<section class="abs slider">
  <div class="slide">
    <div class="photo" role="img" aria-label="Mother and young daughter sharing a hug outdoors in the grass"></div>
    <h1 class="serif">WELCOME TO</h1>
    <h2 class="serif">BEYOND THE TALK THERAPY!</h2>
    <p>I also frequently search the Internet to find a school, camp, classes and therapies for my own kids. I know that a task of finding a place and people who I can trust my kids is not an easy task</p>
    <div class="btn">KNOW MORE</div>
    <div class="dots"><i></i><i></i><i></i><i></i></div>
  </div>
</section>

<p class="abs quote">CLARA IS CONSTANTLY TRYING NEW THINGS TO HELP OUR SON COMMUNICATE... SHE IS WONDERFUL<br>WITH THE CUESTEP SPEECH THERAPY PROGRAM AND TRULY CARES ABOUT OUR SON AND HIS PROGRESS.</p>
<div class="abs rule"></div>
<div class="abs side-bg"></div>

<div class="band blue" style="left:192px;top:409px;width:407px">LATEST BLOG</div>

<article class="post" style="top:451px">
  <h3 class="serif">Pellentesque ipsum purus, accumsan ut nibh non.</h3>
  <p>Duis facilisis ipsum quis dapibus aliquet. Nullam non urna et ipsum convallis facilisis. Aliquam ut varius ligula, eget pulvinar odio. Mauris nec lobortis lectus. Sed eros lectus, iaculis sed hendrerit pretium, fermentum vel risus. Nunc vel arcu id felis consequat euismod vitae non neque. In hac habitasse platea dictumst. Ut sit amet velit eget justo commodo semper. Aenean placerat eget nulla vitae ultricies. Aliquam consectetur dui a ipsum pharetra ornare vitae vitae nunc. Quisque tempor lectus elit, id mollis libero lobortis rhoncus. Integer tellus erat, mollis sed vehicula vel, sagittis id lectus.</p>
  <div class="media">
    <div class="img" role="img" aria-label="Mother and baby looking at a laptop together"></div>
    <p>Pellentesque ipsum purus, accumsan ut nibh non, fringilla tristique metus. Donec venenatis elementum tellus, at aliquet lorem mollis in. Morbi quis vehicula augue, vitae ornare sem. In imperdiet volutpat velit ut aliquet. Donec id ipsum ac elit adipiscing feugiat id quis augue. Nullam commodo neque quis nunc auctor faucibus. Quisque tincidunt volutpat pretium. Mauris sollicitudin risus sem, a rhoncus metus aliquet a. Integer vestibulum molestie pretium.</p>
  </div>
</article>
<div class="share" style="top:676px"><span class="more">KNOW MORE</span><span class="sbtn"><b>Like</b><span>3k</span></span><span class="sbtn"><b>Post</b><span>316</span></span><span class="sbtn"><b>+1</b><span>81</span></span><span class="sbtn"><b class="red">Share</b><span>4.6K</span></span><span class="date">July-22-2103</span></div>

<article class="post" style="top:721px">
  <h3 class="serif">Duis facilisis ipsum quis dapibus aliquet</h3>
  <p>Duis facilisis ipsum quis dapibus aliquet. Nullam non urna et ipsum convallis facilisis. Aliquam ut varius ligula, eget pulvinar odio. Mauris nec lobortis lectus. Sed eros lectus, iaculis sed hendrerit pretium, fermentum vel risus. Nunc vel arcu id felis consequat euismod vitae non neque. In hac habitasse platea dictumst. Ut sit amet velit eget justo commodo semper. Aenean placerat eget nulla vitae ultricies. Aliquam consectetur dui a ipsum pharetra ornare vitae vitae nunc. Quisque tempor lectus elit, id mollis libero lobortis rhoncus. Integer tellus erat, mollis sed vehicula vel, sagittis id lectus.</p>
</article>
<div class="share" style="top:829px"><span class="more">KNOW MORE</span><span class="sbtn"><b>Like</b><span>3k</span></span><span class="sbtn"><b>Post</b><span>316</span></span><span class="sbtn"><b>+1</b><span>81</span></span><span class="sbtn"><b class="red">Share</b><span>4.6K</span></span><span class="date">July-22-2103</span></div>

<article class="post" style="top:873px">
  <h3 class="serif">Aenean egestas aliquet nisl, sed vehicula nisi faucibus</h3>
  <p>Duis facilisis ipsum quis dapibus aliquet. Nullam non urna et ipsum convallis facilisis. Aliquam ut varius ligula, eget pulvinar odio. Mauris nec lobortis lectus. Sed eros lectus, iaculis sed hendrerit pretium, fermentum vel risus. Nunc vel arcu id felis consequat euismod vitae non neque. In hac habitasse platea dictumst.</p>
  <p>Ut sit amet velit eget justo commodo semper. Aenean placerat eget nulla vitae ultricies. Aliquam consectetur dui a ipsum pharetra ornare vitae vitae nunc. Quisque tempor lectus elit, id mollis libero lobortis rhoncus. Integer tellus erat, mollis sed vehicula vel, sagittis id lectus. Pellentesque ipsum purus, accumsan ut nibh non, fringilla tristique metus. Donec venenatis elementum tellus, at aliquet lorem mollis in. Morbi quis vehicula augue, vitae ornare sem. In imperdiet volutpat velit ut aliquet.</p>
</article>
<div class="share" style="top:1012px"><span class="more">KNOW MORE</span><span class="sbtn"><b>Like</b><span>3k</span></span><span class="sbtn"><b>Post</b><span>316</span></span><span class="sbtn"><b>+1</b><span>81</span></span><span class="sbtn"><b class="red">Share</b><span>4.6K</span></span><span class="date">July-22-2103</span></div>

<div class="abs pages"><span class="cur">1</span><span>2</span><span>3</span><span>4</span><span>5</span><span>6</span><span>7</span><span>8</span><span>9</span><span>...</span></div>

<div class="band green" style="left:612px;top:409px;width:156px">MEMBERS WITH</div>
<div class="badge" style="top:452px;height:48px;background:#d9dde3"></div>
<div class="badge" style="top:524px;height:46px;background:#d7dbe8"></div>
<div class="badge" style="top:582px;height:30px;background:#e2e2e2"></div>
<div class="badge" style="top:624px;height:48px;background:#dce7f1"></div>
<div class="badge" style="top:686px;height:36px;background:#5a86b8"></div>

<div class="band green" style="left:612px;top:738px;width:156px">RECENT BLOG</div>
<div class="recent" style="top:779px"><h4>Frozen Door</h4><p>Nulla facilisi. Curabitur at elit ligula, eget hen drerit felis vehicula.</p><small>Jan-11-2013</small></div>
<div class="recent" style="top:837px"><h4>Frozen Door</h4><p>Nulla facilisi. Curabitur at elit ligula, eget hen drerit felis vehicula.</p><small>Jan-11-2013</small></div>
<div class="recent" style="top:897px"><h4>Frozen Door</h4><p>Nulla facilisi. Curabitur at elit ligula, eget hen drerit felis vehicula.</p><small>Jan-11-2013</small></div>

<div class="band green" style="left:612px;top:962px;width:156px">CONTACT US</div>
<div class="abs contact" style="top:997px"><b>Address</b>: 218 Willowbend Ln Maple TX 75000</div>
<div class="abs contact" style="top:1015px"><b>Email</b>: clara@beyondtalkclinic-demo.com</div>
<div class="abs contact" style="top:1033px"><b>Phone</b>: (555)-014-2290</div>

<div class="abs foot-links">Home<span>|</span>About<span>|</span>Treatment Techniques<span>|</span>BLOG<span>|</span>FAQ<span>|</span>Resources</div>
<div class="abs copy">Copyright © Beyond The Talk LLC. &nbsp;All rights reserved.</div>
<div class="abs social"><i style="background:#3b5a98"></i><i style="background:#48b6e2"></i><i style="background:#2a6fa8"></i><i style="background:#f08a24"></i><i style="background:#5aa94a"></i></div>
</body>
</html>
```